Corvel Capital LLC

Need Professional Business cards for New Investment Fund

Target Market(s)

High Quality investors

Industry/Entity Type

Financial

Contact Information for Business Card

Phone Number +1 555 284 6190
Name Lukas Varenko
Title Fund Manager
email lv@FundCorvel.com
Website www.FundCorvel.com

Colors

Designer to choose colors to be used in the design.

Requirements
Must have
• Must have our Logo and all of the above. Must be made so lettering and loge can be raised

```html
<!DOCTYPE html>
<html lang="en">
<head>
<meta charset="utf-8">
<title>Orvessa – Business Card</title>
<link href="https://fonts.googleapis.com/css2?family=Arimo:wght@400;700&display=swap" rel="stylesheet">
<style>
  :root {
    --backdrop: #e9e6e1;
    --card-white: #ffffff;
    --forest: #3c4a3e;
    --forest-deep: #344136;
    --leaf: #4fb848;
    --ink: #3a3f3a;
    --muted: #9a9a9a;
    --rule: #8f8f8f;
  }
  * { box-sizing: border-box; margin: 0; padding: 0; }
  html, body {
    width: 1200px; height: 800px; overflow: hidden;
    background: var(--backdrop);
    font-family: "Arimo", Arial, sans-serif;
  }
  .canvas {
    position: relative; width: 1200px; height: 800px;
    display: flex; align-items: center; justify-content: center; gap: 40px;
  }
  .card {
    position: relative; width: 540px; height: 309px;
    box-shadow: 0 6px 18px rgba(0,0,0,0.18);
    overflow: hidden;
  }
  /* Front */
  .card-front { background: var(--card-white); }
  .identity {
    position: absolute; right: 36px; top: 70px; text-align: right;
  }
  .identity-name { font-size: 19px; font-weight: 700; color: var(--ink); letter-spacing: 0.2px; }
  .identity-title { font-size: 13px; color: var(--muted); margin-top: 3px; }
  .rule-top {
    position: absolute; left: 230px; right: 36px; top: 120px;
    height: 1px; background: var(--rule);
  }
  .brand {
    position: absolute; left: 40px; top: 142px;
    display: flex; align-items: center; gap: 10px;
  }
  .brand-square { width: 16px; height: 16px; background: var(--leaf); }
  .brand-name { font-size: 28px; font-weight: 700; color: var(--forest); letter-spacing: 0.5px; }
  .rule-bottom {
    position: absolute; left: 40px; right: 230px; top: 206px;
    height: 1px; background: var(--rule);
  }
  .contacts {
    position: absolute; left: 40px; top: 220px;
    list-style: none; font-size: 13px; color: var(--muted);
  }
  .contacts li { display: flex; align-items: center; gap: 10px; height: 22px; }
  .contacts svg { width: 13px; height: 13px; flex: none; }
  .contacts strong { color: var(--muted); font-weight: 700; }
  /* Back */
  .card-back { background: var(--forest); }
  .back-pattern {
    position: absolute; inset: 0;
    background: linear-gradient(135deg, var(--forest) 0%, var(--forest-deep) 100%);
  }
  .back-brand {
    position: absolute; right: 150px; top: 200px;
    font-size: 22px; font-weight: 700; color: var(--card-white); letter-spacing: 0.5px;
  }
</style>
</head>
<body>
<main class="canvas">
  <section class="card card-front" aria-label="Business card front">
    <div class="identity">
      <p class="identity-name">Lukas Varenko</p>
      <p class="identity-title">Fund Manager</p>
    </div>
    <div class="rule-top"></div>
    <div class="brand">
      <span class="brand-square"></span>
      <span class="brand-name">Orvessa</span>
    </div>
    <div class="rule-bottom"></div>
    <ul class="contacts">
      <li>
        <svg viewBox="0 0 16 16" aria-hidden="true"><path fill="#3a3f3a" d="M3.5 1.5l2.5 0 1 3.5-1.8 1.2a8 8 0 0 0 4.6 4.6L11 9l3.5 1v2.5c0 1-1 2-2 2A11 11 0 0 1 1.5 3.5c0-1 1-2 2-2z"/></svg>
        <span>+1 555 284 6190</span>
      </li>
      <li>
        <svg viewBox="0 0 16 16" aria-hidden="true"><rect x="1" y="3" width="14" height="10" fill="#3a3f3a"/><path d="M1.5 3.5L8 9l6.5-5.5" stroke="#fff" stroke-width="1.3" fill="none"/></svg>
        <span>lv@FundCorvel.com</span>
      </li>
      <li>
        <svg viewBox="0 0 16 16" aria-hidden="true"><circle cx="8" cy="8" r="6.5" fill="none" stroke="#3a3f3a" stroke-width="1.5"/><ellipse cx="8" cy="8" rx="2.8" ry="6.5" fill="none" stroke="#3a3f3a" stroke-width="1.2"/><path d="M1.5 8h13" stroke="#3a3f3a" stroke-width="1.2"/></svg>
        <span>www.<strong>FundCorvel</strong>.com</span>
      </li>
    </ul>
  </section>

  <section class="card card-back" aria-label="Business card back">
    <div class="back-pattern" role="img" aria-label="Repeating tonal brand pattern in dark green"></div>
    <div class="back-brand">Orvessa</div>
  </section>
</main>
</body>
</html>
```